Expedition Cruise Sales Website for the Polar Regions (Antarctica & Arctic)

This will be a website for selling cruises.
This site should have a homepage, a ship page, destinations, and itineraries.
I have created a file specifying each page, and it is attached.
Pages:
1. Home
2. Cruise Lines
- 2.1 Ships
3. Destinations
- 3.1 Region - 3.2 Country - 3.3 City
4. Itineraries
- 4.1 Itinerary
5. Blog / Travel Tips 6. About Us
7. Contact
Please take a look on the attached pdf
Target Market(s)
Expedition Travelers
Coding
Coded - Design and coding required
Number of Pages Required
5+ page
Font styles to use
Look and feel
Each slider illustrates characteristics of the customer's brand and the style your logo design should communicate.

```html
<!DOCTYPE html>
<html lang="en">
<head>
<meta charset="UTF-8">
<title>Polarvia.co — Cruise Lines</title>
<link href="https://fonts.googleapis.com/css2?family=Outfit:wght@300;400;500;600;700&family=Poppins:wght@400;500;600&display=swap" rel="stylesheet">
<style>
:root{
  --navy:#0f1d3d;
  --navy-deep:#0b1733;
  --blue:#1877f2;
  --blue-bright:#1a7cf5;
  --sky:#d5e6fb;
  --pale:#eef3fb;
  --ink:#1c2233;
  --muted:#4a5060;
  --star:#f29a1f;
  --green:#1fa463;
  --white:#ffffff;
}
*{box-sizing:border-box;margin:0;padding:0}
html,body{width:1200px;height:4392px;overflow:hidden}
body{font-family:"Poppins",sans-serif;color:var(--ink);background:var(--white);position:relative}
h1,h2,h3,h4,.display{font-family:"Outfit",sans-serif}

/* Header / hero */
.hero{position:relative;height:409px;background:linear-gradient(180deg,#3b4350 0%,#6a6f72 40%,#8b8a83 58%,#3d4a57 72%,#26313d 100%)}
.nav{position:absolute;top:0;left:0;right:0;height:96px;display:flex;align-items:center;padding:0 112px}
.brand{display:flex;align-items:center;gap:10px;font-family:"Outfit",sans-serif;font-weight:600;font-size:20px;color:var(--white)}
.brand-dot{width:14px;height:14px;border-radius:50%;background:var(--white)}
.nav-links{display:flex;gap:30px;margin-left:auto;margin-right:32px;font-size:12px;color:var(--white)}
.nav-links span{display:flex;align-items:center;gap:4px}
.btn-contact{background:var(--blue);color:var(--white);font-size:12px;padding:11px 24px;border-radius:22px;border:2px solid rgba(255,255,255,.5)}
.hero-title{position:absolute;top:178px;left:0;right:0;text-align:center;color:var(--white)}
.hero-title .lead{font-family:"Outfit",sans-serif;font-weight:300;font-size:38px;line-height:1.1}
.hero-title .main{font-family:"Outfit",sans-serif;font-weight:700;font-size:50px;line-height:1.05}

/* Intro */
.intro{position:relative;height:321px;background:var(--sky)}
.intro-photo{position:absolute;left:0;top:0;width:460px;height:360px;background:radial-gradient(ellipse at 40% 55%,#f4f7fb 0%,#cfdde8 40%,rgba(213,230,251,0) 75%)}
.intro-ship{position:absolute;right:0;bottom:0;width:210px;height:130px;background:linear-gradient(90deg,rgba(213,230,251,0),#e9eff6)}
.intro-text{position:absolute;left:482px;top:94px;width:560px;font-size:19.5px;line-height:29px;color:var(--ink)}
.intro-text strong{font-weight:600}

.section-title{height:192px;display:flex;align-items:center;justify-content:center;font-size:45px;font-weight:600;color:var(--navy);padding-top:42px}

/* Features */
.features{display:flex;flex-direction:column;gap:38px}
.feature{position:relative;display:grid;grid-template-columns:592px 1fr;height:474px}
.feature.flip{grid-template-columns:1fr 593px}
.feature-photo{height:474px}
.feature.flip .feature-photo{order:2}
.badge{position:absolute;top:29px;width:51px;height:44px;border-radius:10px;background:var(--blue-bright);color:var(--white);font-family:"Outfit",sans-serif;font-size:22px;display:flex;align-items:center;justify-content:center}
.feature .badge{left:542px}
.feature.flip .badge{left:607px}
.feature-body{padding:24px 40px 0 39px}
.feature.flip .feature-body{padding-left:111px}
.feature-name{font-size:33px;font-weight:600;color:var(--navy);line-height:1.2}
.feature-tag{font-family:"Outfit",sans-serif;font-weight:600;font-size:20px;color:var(--blue);margin-top:4px;line-height:1.3}
.meta{display:flex;align-items:center;gap:40px;font-size:12.5px;color:var(--muted);margin-top:14px}
.rating{display:flex;align-items:center;gap:5px}
.stars{display:flex;gap:2px}
.meta small{font-size:10px}
.fleet{display:flex;align-items:center;gap:6px}
.desc{font-size:12.5px;line-height:20px;color:#3a3f4c;margin-top:22px;max-width:450px}
.fleet-title{font-family:"Outfit",sans-serif;font-weight:600;font-size:17px;color:var(--navy);margin-top:28px}
.ships{list-style:none;font-size:12.5px;line-height:20px;color:#3a3f4c;margin-top:8px}
.ships li::before{content:"•";margin:0 8px 0 6px}
.btn-pill{display:inline-flex;align-items:center;gap:12px;background:var(--navy);color:var(--white);font-size:13px;padding:4px 4px 4px 18px;border-radius:24px;margin-top:22px}
.btn-pill .arrow{width:30px;height:30px;border-radius:50%;background:var(--blue-bright);display:flex;align-items:center;justify-content:center}

/* Reviews */
.reviews{position:absolute;top:3439px;left:0;width:1200px;height:578px;background:var(--pale)}
.reviews-kicker{position:absolute;top:84px;width:100%;text-align:center;font-family:"Outfit",sans-serif;font-size:24px;color:var(--navy)}
.reviews-title{position:absolute;top:112px;width:100%;text-align:center;font-size:50px;font-weight:600;color:var(--navy)}
.review-card{position:absolute;top:206px;width:278px;height:154px;background:var(--white);padding:28px 30px;box-shadow:0 2px 8px rgba(20,40,80,.06)}
.review-head{display:flex;align-items:center;gap:6px;font-size:10px;color:#7a7f8a}
.score{display:flex;gap:2px}
.score i{display:block;width:12px;height:12px;background:var(--green)}
.verified{width:11px;height:11px;border-radius:50%;background:#8f949c}
.review-card h4{font-family:"Poppins",sans-serif;font-size:11px;font-weight:600;margin-top:8px}
.review-card p{font-size:9px;line-height:13px;color:#555;margin-top:4px}
.review-card .who{font-size:8.5px;color:#777;margin-top:4px}
.review-card .who b{color:#333;font-weight:600}
.review-card .note{font-size:9px;color:#333;margin-top:10px}
.slider-btn{position:absolute;top:266px;width:34px;height:34px;border-radius:50%;display:flex;align-items:center;justify-content:center}
.slider-btn.prev{left:111px;background:var(--navy)}
.slider-btn.next{left:1054px;background:var(--blue-bright)}

/* Footer */
.footer{position:absolute;top:4017px;left:0;width:1200px;height:375px;background:var(--navy-deep);color:var(--white)}
.cta{position:absolute;top:3863px;left:112px;width:971px;height:243px;background:linear-gradient(180deg,#1b7ef2,#1264d6);text-align:center;color:var(--white);z-index:2}
.cta h2{font-size:44px;font-weight:600;margin-top:30px}
.cta p{font-size:13px;line-height:20px;width:640px;margin:12px auto 0}
.cta .btn-dark{display:inline-block;margin-top:22px;background:var(--navy);color:var(--white);font-size:13px;padding:10px 18px;border-radius:20px}
.footer-brand{position:absolute;left:112px;top:165px;display:flex;align-items:center;gap:10px;font-family:"Outfit",sans-serif;font-weight:600;font-size:34px}
.footer-brand .brand-dot{width:22px;height:22px}
.footer-col{position:absolute;top:150px}
.footer-col h3{font-size:20px;font-weight:600}
.footer-col p{font-size:10px;line-height:15px;color:#c9d2e6;margin-top:6px}
.col-chat{left:433px;width:250px}
.col-community{left:810px;width:280px}
.btn-join{display:inline-block;margin-top:14px;background:var(--blue-bright);font-size:11px;padding:8px 16px;border-radius:16px}
.subscribe{margin-top:18px;width:274px;height:36px;background:var(--white);border-radius:18px;display:flex;align-items:center;justify-content:space-between;padding:3px;border:2px solid var(--blue)}
.subscribe span{font-size:9px;color:#999;padding-left:24px}
.subscribe b{background:var(--blue-bright);color:var(--white);font-weight:500;font-size:11px;padding:7px 12px;border-radius:14px}
.footer-rule{position:absolute;top:319px;left:112px;width:971px;height:1px;background:rgba(255,255,255,.18)}
.footer-links{position:absolute;top:340px;left:112px;display:flex;gap:26px;font-size:11.5px}
.socials{position:absolute;top:340px;left:1004px;display:flex;gap:10px}
.socials i{width:15px;height:15px;border-radius:50%;background:var(--white);display:block}
</style>
</head>
<body>

<header class="hero" role="img" aria-label="Large white cruise ship moored at a harbour at dusk">
  <nav class="nav">
    <div class="brand"><span class="brand-dot"></span>Polarvia.co</div>
    <div class="nav-links">
      <span>Home</span>
      <span>Cruise Lines <svg width="7" height="5" viewBox="0 0 7 5"><path d="M1 1l2.5 2.5L6 1" stroke="#fff" fill="none"/></svg></span>
      <span>Destinations <svg width="7" height="5" viewBox="0 0 7 5"><path d="M1 1l2.5 2.5L6 1" stroke="#fff" fill="none"/></svg></span>
      <span>Itineraries <svg width="7" height="5" viewBox="0 0 7 5"><path d="M1 1l2.5 2.5L6 1" stroke="#fff" fill="none"/></svg></span>
      <span>Blog / Travel Tips</span>
      <span>About</span>
    </div>
    <div class="btn-contact">Contact</div>
  </nav>
  <div class="hero-title">
    <div class="lead">Explore the World’s</div>
    <div class="main">Best Cruise Lines</div>
  </div>
</header>

<section class="intro">
  <div class="intro-photo" role="img" aria-label="Cruise ship sailing over turquoise water and clouds"></div>
  <div class="intro-ship" role="img" aria-label="Faint cruise ship in the distance"></div>
  <p class="intro-text">At <strong>Polarvia.co</strong>, we partner with top cruise lines to bring you exceptional voyages across the globe. Whether you seek luxurious amenities, family-friendly experiences, or thrilling expeditions, our cruise lines offer something for every traveler.</p>
</section>

<h2 class="section-title">Our Featured Cruise Lines</h2>

<svg width="0" height="0" style="position:absolute">
  <defs>
    <symbol id="star" viewBox="0 0 10 10"><path d="M5 .5l1.4 2.9 3.1.4-2.3 2.2.6 3.1L5 7.6 2.2 9.1l.6-3.1L.5 3.8l3.1-.4z"/></symbol>
    <symbol id="ship" viewBox="0 0 12 12"><path d="M4 1h3v2h2v3l2 1-2 4H3L1 7l2-1V3h1z" fill="#1c2233"/></symbol>
    <symbol id="arrow" viewBox="0 0 12 12"><path d="M2 6h8M7 3l3 3-3 3" stroke="#fff" stroke-width="1.4" fill="none"/></symbol>
  </defs>
</svg>

<div class="features">
  <article class="feature">
    <div class="feature-photo" role="img" aria-label="Couple with shopping bags walking along a marina pier beside yachts" style="background:linear-gradient(160deg,#dfe6ee,#a9b5c2 55%,#3e5672)"></div>
    <div class="badge">01</div>
    <div class="feature-body">
      <h3 class="feature-name">Oceanic Voyages</h3>
      <div class="feature-tag">Experience Unmatched Luxury &amp; Service</div>
      <div class="meta">
        <div class="rating">Rating <span class="stars"><svg width="13" height="13" fill="#f29a1f"><use href="#star"/></svg><svg width="13" height="13" fill="#f29a1f"><use href="#star"/></svg><svg width="13" height="13" fill="#f29a1f"><use href="#star"/></svg><svg width="13" height="13" fill="#f29a1f"><use href="#star"/></svg><svg width="13" height="13" fill="#f29a1f"><use href="#star"/></svg></span> <small>(4.9/5)</small></div>
        <div class="fleet"><svg width="12" height="12"><use href="#ship"/></svg>Fleet Size: <small>15 Ships</small></div>
      </div>
      <p class="desc">Oceanic Voyages is renowned for its elegant ships, world-class dining, and personalized service. Designed for travelers seeking a refined cruising experience, their fleet offers spacious suites, gourmet restaurants, and exclusive shore excursions.</p>
      <h4 class="fleet-title">Ships in the Fleet:</h4>
      <ul class="ships"><li>Oceanic Majesty</li><li>Oceanic Serenity</li><li>Oceanic Explorer</li><li>Oceanic Star</li><li>More...</li></ul>
      <span class="btn-pill">Explore Oceanic Voyages <span class="arrow"><svg width="12" height="12"><use href="#arrow"/></svg></span></span>
    </div>
  </article>

  <article class="feature flip">
    <div class="feature-photo" role="img" aria-label="Family standing on a wooden pier by the calm sea" style="background:linear-gradient(180deg,#eef1f2,#c9d3d8 50%,#9b8b76)"></div>
    <div class="badge">02</div>
    <div class="feature-body">
      <h3 class="feature-name">Blue Horizon Cruises</h3>
      <div class="feature-tag">Family-Friendly Fun &amp; Adventure</div>
      <div class="meta">
        <div class="rating">Rating <span class="stars"><svg width="13" height="13" fill="#f29a1f"><use href="#star"/></svg><svg width="13" height="13" fill="#f29a1f"><use href="#star"/></svg><svg width="13" height="13" fill="#f29a1f"><use href="#star"/></svg><svg width="13" height="13" fill="#f29a1f"><use href="#star"/></svg><svg width="13" height="13" fill="#cfcfcf"><use href="#star"/></svg></span> <small>(4.5/5)</small></div>
        <div class="fleet"><svg width="12" height="12"><use href="#ship"/></svg>Fleet Size: <small>20 Ships</small></div>
      </div>
      <p class="desc">Blue Horizon Cruises caters to families and adventure seekers with entertainment-packed ships, water parks, kids’ clubs, and exciting shore excursions. Perfect for multi-generational travelers looking for fun-filled vacations.</p>
      <h4 class="fleet-title">Ships in the Fleet:</h4>
      <ul class="ships"><li>Blue Wave</li><li>Blue Odyssey</li><li>Horizon Breeze</li><li>Ocean Quest</li><li>More...</li></ul>
      <span class="btn-pill">Discover Blue Horizon Cruises <span class="arrow"><svg width="12" height="12"><use href="#arrow"/></svg></span></span>
    </div>
  </article>

  <article class="feature">
    <div class="feature-photo" role="img" aria-label="Cruise ship sailing through a green fjord" style="background:linear-gradient(180deg,#c9dbea,#9fbcd2 35%,#3f6a4c 55%,#2f6f86 75%,#1f5168)"></div>
    <div class="badge">03</div>
    <div class="feature-body">
      <h3 class="feature-name">Arctic Explorer Expeditions</h3>
      <div class="feature-tag">Discover the World’s Most Remote Destinations</div>
      <div class="meta">
        <div class="rating">Rating <span class="stars"><svg width="13" height="13" fill="#f29a1f"><use href="#star"/></svg><svg width="13" height="13" fill="#f29a1f"><use href="#star"/></svg><svg width="13" height="13" fill="#f29a1f"><use href="#star"/></svg><svg width="13" height="13" fill="#f29a1f"><use href="#star"/></svg><svg width="13" height="13" fill="#f29a1f"><use href="#star"/></svg></span> <small>(4.8/5)</small></div>
        <div class="fleet"><svg width="12" height="12"><use href="#ship"/></svg>Fleet Size: <small>10 Ships</small></div>
      </div>
      <p class="desc">For those who seek adventure beyond the ordinary, Arctic Explorer Expeditions specializes in voyages to Antarctica, the Arctic, and other untouched destinations. Experience wildlife encounters, icebreaker journeys, and expert-led excursions.</p>
      <h4 class="fleet-title">Ships in the Fleet:</h4>
      <ul class="ships"><li>Polar Adventurer</li><li>Arctic Pioneer</li><li>Icebreaker Voyager</li><li>Northern Spirit</li><li>More...</li></ul>
      <span class="btn-pill">View Arctic Explorer Expeditions <span class="arrow"><svg width="12" height="12"><use href="#arrow"/></svg></span></span>
    </div>
  </article>

  <article class="feature flip">
    <div class="feature-photo" role="img" aria-label="Man in a linen suit sitting on a sunny deck terrace" style="background:linear-gradient(150deg,#dfe8ee,#b8c7cf 45%,#6f8a6b 70%,#c9b89a)"></div>
    <div class="badge">04</div>
    <div class="feature-body">
      <h3 class="feature-name">Celestial Cruises</h3>
      <div class="feature-tag">Elegant Voyages Through Historic &amp; Scenic Destinations</div>
      <div class="meta">
        <div class="rating">Rating <span class="stars"><svg width="13" height="13" fill="#f29a1f"><use href="#star"/></svg><svg width="13" height="13" fill="#f29a1f"><use href="#star"/></svg><svg width="13" height="13" fill="#f29a1f"><use href="#star"/></svg><svg width="13" height="13" fill="#f29a1f"><use href="#star"/></svg><svg width="13" height="13" fill="#cfcfcf"><use href="#star"/></svg></span> <small>(4.6/5)</small></div>
        <div class="fleet"><svg width="12" height="12"><use href="#ship"/></svg>Fleet Size: <small>12 Ships</small></div>
      </div>
      <p class="desc">Celestial Cruises offers culturally immersive journeys through Europe, the Mediterranean, and Asia. Enjoy onboard lectures, fine dining, and exclusive guided tours at world-renowned ports.</p>
      <h4 class="fleet-title">Ships in the Fleet:</h4>
      <ul class="ships"><li>Celestial Harmony</li><li>Star of Athens</li><li>Mediterranean Pearl</li><li>Eastern Sun</li><li>More...</li></ul>
      <span class="btn-pill">Explore Celestial Cruises <span class="arrow"><svg width="12" height="12"><use href="#arrow"/></svg></span></span>
    </div>
  </article>

  <article class="feature">
    <div class="feature-photo" role="img" aria-label="Ship deck pool overlooking the open ocean under a blue sky" style="background:linear-gradient(180deg,#2e6fa8,#6ea4cf 40%,#2b7ea8 62%,#3ab0d6 80%,#8a9aa6)"></div>
    <div class="badge">05</div>
    <div class="feature-body">
      <h3 class="feature-name">Paradise Island Cruises</h3>
      <div class="feature-tag">Luxury, Relaxation, and Tropical Getaways</div>
      <div class="meta">
        <div class="rating">Rating <span class="stars"><svg width="13" height="13" fill="#f29a1f"><use href="#star"/></svg><svg width="13" height="13" fill="#f29a1f"><use href="#star"/></svg><svg width="13" height="13" fill="#f29a1f"><use href="#star"/></svg><svg width="13" height="13" fill="#f29a1f"><use href="#star"/></svg><svg width="13" height="13" fill="#f29a1f"><use href="#star"/></svg></span> <small>(4.7/5)</small></div>
        <div class="fleet"><svg width="12" height="12"><use href="#ship"/></svg>Fleet Size: <small>18 Ships</small></div>
      </div>
      <p class="desc">Paradise Island Cruises is known for its all-inclusive experiences, island-hopping itineraries, and five-star resort-style ships. Designed for relaxation seekers, these cruises take you to the Caribbean, the Maldives, and other idyllic destinations.</p>
      <h4 class="fleet-title">Ships in the Fleet:</h4>
      <ul class="ships"><li>Paradise Dream</li><li>Island Serenity</li><li>Ocean Haven</li><li>Tropical Voyager</li><li>More...</li></ul>
      <span class="btn-pill">Discover Paradise Island Cruises <span class="arrow"><svg width="12" height="12"><use href="#arrow"/></svg></span></span>
    </div>
  </article>
</div>

<section class="reviews">
  <div class="reviews-kicker">Real Customer Reviews</div>
  <h2 class="reviews-title">What Our Travelers Say</h2>
  <div class="slider-btn prev"><svg width="12" height="12" style="transform:rotate(180deg)"><use href="#arrow"/></svg></div>
  <div class="review-card" style="left:162px">
    <div class="review-head"><span class="score"><i></i><i></i><i></i><i></i><i></i></span><span class="verified"></span>Verified</div>
    <h4>An unforgettable experience!</h4>
    <p>The ship was luxurious, and the destinations were beyond stunning.</p>
    <div class="who"><b>Sarah L.</b>&nbsp; 6 days ago</div>
    <div class="note">Showing our 4 &amp; 5 star reviews</div>
  </div>
  <div class="review-card" style="left:460px">
    <div class="review-head"><span class="score"><i></i><i></i><i></i><i></i><i></i></span><span class="verified"></span>Verified</div>
    <h4>Our family had the best vacation</h4>
    <p>ever! Everything was so well planned, and the service was top-notch.</p>
    <div class="who"><b>The Johnsons,</b>&nbsp; 6 days ago</div>
    <div class="note">Showing our 4 &amp; 5 star reviews</div>
  </div>
  <div class="review-card" style="left:760px">
    <div class="review-head"><span class="score"><i></i><i></i><i></i><i></i><i></i></span><span class="verified"></span>Verified</div>
    <h4>I booked a last-minute deal,</h4>
    <p>and it was the best decision ever! Amazing value for such a fantastic trip.</p>
    <div class="who"><b>Michael R.</b>&nbsp; 6 days ago</div>
    <div class="note">Showing our 4 &amp; 5 star reviews</div>
  </div>
  <div class="slider-btn next"><svg width="12" height="12"><use href="#arrow"/></svg></div>
</section>

<section class="cta">
  <h2>Find the Perfect Cruise Line for You</h2>
  <p>Each cruise line offers a unique experience tailored to different types of travelers. Whether you prefer an adventurous expedition, a luxurious escape, or a family-friendly voyage, Polarvia.co connects you with the perfect cruise.</p>
  <span class="btn-dark">Browse All Cruise Lines</span>
</section>

<footer class="footer">
  <div class="footer-brand"><span class="brand-dot"></span>Polarvia.co</div>
  <div class="footer-col col-chat">
    <h3>Join Our ChatLine List</h3>
    <p>Prefer ChatLine updates? Get real-time cruise deals sent straight to your phone.</p>
    <span class="btn-join">Join Now</span>
  </div>
  <div class="footer-col col-community">
    <h3>Join Our Cruise Community</h3>
    <p>Be the first to know about new cruise deals, exclusive promotions, and travel tips.</p>
    <div class="subscribe"><span>Enter your email</span><b>Subscribe Now</b></div>
  </div>
  <div class="footer-rule"></div>
  <div class="footer-links">
    <span>Home</span><span>Cruise Lines</span><span>Destinations</span><span>Itineraries</span><span>Blog</span><span>Travel Tips</span><span>About</span><span>Contact</span>
  </div>
  <div class="socials"><i></i><i></i><i></i></div>
</footer>

</body>
</html>
```